Membership Based Medical Practice Website

We need a functioning website for a new Membership based medical practice. There will be an enrollment fee and a monthly fee. We would like to see designs that are modern, simple. Should use neutral light colors. Examples of sites we like are www.kellanmoorclinic.com and https://fernholtcare.com/ We also have a link that when "Join Now" is clicked it will go to the signup website.

Target Market(s)

Gay Men, local population, Age group 20 to 60's.

Industry/Entity Type

Medical

Coding

Coded - Design and coding required

Number of Pages Required

5+ page

Font styles to use
Sans Serif

Colors
ffffff
cee9f5
ecf7fb
cfeae6
edf8f6
aaaaaa
e9e9e9
dbdbdb
fff3d1

Requirements
Must have
• Logo and header on every page. Clean, simple design, clear content, mobile compatible.
• Must use Wordpress
Nice to have
• Ideas should come from kellanmoorclinic.com
• Easy to read
Should not have
• Generic patient pictures, bold colors.
• Should not copy from above websites.

```html
<!DOCTYPE html>
<html lang="en">
<head>
<meta charset="utf-8">
<title>Contact Us – Lakeshore Infectious Disease Specialists</title>
<link href="https://fonts.googleapis.com/css2?family=Lato:wght@400;700;900&display=swap" rel="stylesheet">
<style>
  :root {
    --white: #ffffff;
    --ink: #3d3d3d;
    --ink-dark: #111111;
    --mint: #cfeae6;
    --sky-band: #e6f3f9;
    --field-border: #bcbcbc;
    --gold: #c9a45c;
    --grey: #6b6b6b;
  }
  * { box-sizing: border-box; margin: 0; padding: 0; }
  html, body { width: 1200px; height: 1069px; overflow: hidden; background: var(--white); }
  body { font-family: 'Lato', sans-serif; color: var(--ink); position: relative; }

  .site-header { position: absolute; left: 0; top: 0; width: 1200px; height: 143px; }
  .brand { position: absolute; left: 73px; top: 40px; display: flex; align-items: center; gap: 12px; }
  .brand-mark { width: 40px; height: 40px; border-radius: 50%; border: 2px solid var(--gold); }
  .brand-name { font-size: 14px; font-weight: 400; color: var(--ink); line-height: 1.35; width: 200px; text-transform: uppercase; letter-spacing: 1px; }

  .main-nav { position: absolute; top: 66px; left: 443px; display: flex; font-size: 15px; font-weight: 700; color: var(--ink); }
  .main-nav a { color: inherit; text-decoration: none; margin-right: 42px; letter-spacing: .3px; }
  .main-nav a:last-child { margin-right: 0; }
  .join-button { position: absolute; left: 1006px; top: 55px; width: 120px; height: 42px; border-radius: 21px; background: var(--mint); color: var(--ink); font-weight: 700; font-size: 16px; letter-spacing: 1px; display: flex; align-items: center; justify-content: center; text-decoration: none; }

  .hero { position: absolute; left: 0; top: 143px; width: 1200px; height: 187px;
    background: linear-gradient(180deg, #8c9590 0%, #6f7a6c 35%, #56644a 60%, #3a3f37 100%); }
  .hero h1 { position: absolute; width: 100%; top: 60px; text-align: center; color: var(--white); font-size: 44px; font-weight: 900; letter-spacing: .5px; }

  .contact-band { position: absolute; left: 0; top: 330px; width: 1200px; height: 555px; background: var(--sky-band); }
  .section-title { position: absolute; top: 62px; font-size: 34px; font-weight: 400; color: var(--ink); letter-spacing: .3px; }
  .booking-title { left: 74px; }
  .map-title { left: 614px; }

  .field { position: absolute; background: var(--white); border: 1px solid var(--field-border); border-radius: 22px; font-size: 15px; color: var(--ink-dark); padding: 0 23px; display: flex; align-items: center; }
  .field-name { left: 75px; top: 136px; width: 249px; height: 43px; }
  .field-phone { left: 338px; top: 136px; width: 249px; height: 43px; }
  .field-email { left: 75px; top: 193px; width: 513px; height: 43px; }
  .field-message { left: 75px; top: 252px; width: 513px; height: 116px; align-items: flex-start; padding-top: 12px; border-radius: 18px; }
  .submit-button { position: absolute; left: 75px; top: 389px; width: 179px; height: 50px; border-radius: 25px; background: var(--mint); font-size: 16px; font-weight: 700; letter-spacing: .5px; display: flex; align-items: center; justify-content: center; color: var(--ink); }
  .office-hours { position: absolute; left: 75px; top: 482px; font-size: 15px; font-weight: 700; color: var(--ink-dark); }

  .location-map { position: absolute; left: 614px; top: 134px; width: 512px; height: 305px; border-radius: 10px;
    background: linear-gradient(135deg, #e9ecdf 0%, #eef0ea 45%, #dde8d4 100%); }

  .site-footer { position: absolute; left: 0; top: 885px; width: 1200px; height: 184px; }
  .footer-nav { position: absolute; top: 52px; width: 100%; display: flex; justify-content: center; font-size: 15px; font-weight: 700; color: var(--ink); }
  .footer-nav a { color: inherit; text-decoration: none; margin: 0 21px; }
  .copyright { position: absolute; top: 85px; width: 100%; text-align: center; font-size: 14px; color: var(--ink); }
  .social-links { position: absolute; top: 118px; left: 0; width: 100%; display: flex; justify-content: center; gap: 19px; }
  .social-links span { width: 19px; height: 19px; border-radius: 50%; background: var(--grey); display: block; }
</style>
</head>
<body>
  <header class="site-header">
    <div class="brand">
      <span class="brand-mark"></span>
      <span class="brand-name">Lakeshore Infectious Disease Specialists</span>
    </div>
    <nav class="main-nav">
      <a href="#">HOME</a><a href="#">SPECIALTIES</a><a href="#">PRICING</a><a href="#">ABOUT US</a><a href="#">FAQ</a><a href="#">BLOG</a>
    </nav>
    <a class="join-button" href="#">JOIN US</a>
  </header>

  <section class="hero" role="img" aria-label="Photo of a quiet country road through green fields with grazing sheep">
    <h1>Contact Us</h1>
  </section>

  <main class="contact-band">
    <h2 class="section-title booking-title">Book Appointment</h2>
    <div class="field field-name">Name</div>
    <div class="field field-phone">PhoneNo</div>
    <div class="field field-email">Email Address</div>
    <div class="field field-message">Message</div>
    <div class="submit-button">SUBMIT</div>
    <p class="office-hours">Office hours by appointment only</p>

    <h2 class="section-title map-title">Location Map</h2>
    <div class="location-map" role="img" aria-label="Street map showing the practice location"></div>
  </main>

  <footer class="site-footer">
    <nav class="footer-nav">
      <a href="#">HOME</a><a href="#">SPECIALTIES</a><a href="#">PRICING</a><a href="#">ABOUT US</a><a href="#">FAQ</a><a href="#">BLOG</a>
    </nav>
    <p class="copyright">Copyright © 2019 CompanyName All Rights Reserved.</p>
    <div class="social-links" aria-label="Social media links">
      <span></span><span></span><span></span><span></span><span></span>
    </div>
  </footer>
</body>
</html>
```